Small Business Broker Business Card Design

A business card design for a small business brokerage, which is a financial service, not unlike real estate brokerage, but for small businesses such as laundromats, pizza shops, restaurants, cleaners etc. The designs should all be simple, more conservative in nature, using the colors and font of the logo. Again, think real estate Brokerage as a business context
Contact Information for Business Card
Name: Glen R. Harlow. Title: Small Business Advisor. Email: g.harlow@bayfieldcapitalworks.example. Mobile: (555) 274-3918. Office: (555) 806-2147. www.bayfieldcapitalworks.example

```html
<!DOCTYPE html>
<html lang="en">
<head>
<meta charset="utf-8">
<title>Bayfield Capital Works – Business Card</title>
<link rel="stylesheet" href="https://fonts.googleapis.com/css2?family=Montserrat:wght@400;500;600;700&display=swap">
<style>
  :root {
    --navy: #1c3668;
    --green: #8cc63f;
    --ink: #1a1a1a;
    --paper: #ffffff;
    --backdrop: #e9e9e9;
  }
  * { box-sizing: border-box; margin: 0; padding: 0; }
  html, body { width: 1093px; height: 1200px; overflow: hidden; }
  body {
    background: var(--backdrop);
    font-family: "Montserrat", Arial, sans-serif;
    position: relative;
  }
  .card {
    position: absolute;
    left: 265px;
    width: 581px;
    height: 364px;
    border-radius: 16px;
    overflow: hidden;
  }
  .card--front { top: 225px; background: var(--paper); }
  .card--back { top: 615px; background: var(--green); }

  /* Front */
  .brand {
    position: absolute;
    left: 20px;
    width: 236px;
    top: 150px;
    text-align: center;
  }
  .brand__mark {
    display: block;
    width: 42px;
    height: 42px;
    margin: 0 auto 14px;
    background: var(--navy);
  }
  .brand__name {
    color: var(--navy);
    font-weight: 700;
    font-size: 12.5px;
    letter-spacing: 0.1px;
    white-space: nowrap;
  }
  .brand__tagline {
    margin-top: 3px;
    color: var(--green);
    font-weight: 600;
    font-size: 6.4px;
    letter-spacing: 0.8px;
    text-transform: uppercase;
    white-space: nowrap;
  }
  .divider {
    position: absolute;
    left: 271px;
    top: 116px;
    width: 1.5px;
    height: 148px;
    background: var(--navy);
  }
  .person {
    position: absolute;
    left: 281px;
    top: 114px;
  }
  .person__name {
    color: var(--navy);
    font-weight: 700;
    font-size: 21px;
    line-height: 1.1;
  }
  .person__title {
    color: var(--ink);
    font-weight: 500;
    font-size: 13px;
    margin-top: 1px;
  }
  .contacts {
    position: absolute;
    left: 284px;
    top: 184px;
    list-style: none;
  }
  .contacts__item {
    display: flex;
    align-items: center;
    height: 19.5px;
    color: var(--ink);
    font-size: 12.5px;
    font-weight: 500;
    white-space: nowrap;
  }
  .contacts__item:nth-child(2) { margin-top: 4px; }
  .contacts__icon {
    width: 12px;
    height: 12px;
    margin-right: 9px;
    fill: var(--navy);
    flex: none;
  }

  /* Back */
  .back-brand {
    position: absolute;
    left: 0;
    right: 0;
    top: 86px;
    text-align: center;
  }
  .back-brand__mark {
    display: block;
    width: 96px;
    height: 96px;
    margin: 0 auto 42px;
    background: var(--navy);
  }
  .back-brand__name {
    color: var(--navy);
    font-weight: 700;
    font-size: 26px;
    line-height: 1.05;
    white-space: nowrap;
  }
  .back-brand__tagline {
    margin-top: 5px;
    color: var(--paper);
    font-weight: 600;
    font-size: 12.6px;
    letter-spacing: 1.7px;
    text-transform: uppercase;
    white-space: nowrap;
  }
</style>
</head>
<body>

<section class="card card--front">
  <div class="brand">
    <span class="brand__mark"></span>
    <p class="brand__name">BAYFIELD CAPITAL WORKS, INC</p>
    <p class="brand__tagline">Trusted guidance for every local ownership move</p>
  </div>

  <div class="divider"></div>

  <div class="person">
    <h1 class="person__name">Glen R. Harlow</h1>
    <p class="person__title">Small Business Advisor</p>
  </div>

  <ul class="contacts">
    <li class="contacts__item">
      <svg class="contacts__icon" viewBox="0 0 24 24" aria-hidden="true"><path d="M2 9c0-3 5-5 10-5s10 2 10 5v2h-5V8.5c-1.5-.5-3-.7-5-.7s-3.5.2-5 .7V11H2z"/><path d="M7 11l-3 8h16l-3-8h-3v2h-4v-2z"/></svg>
      (555) 806-2147
    </li>
    <li class="contacts__item">
      <svg class="contacts__icon" viewBox="0 0 24 24" aria-hidden="true"><path d="M6.6 10.8a15 15 0 0 0 6.6 6.6l2.2-2.2c.3-.3.7-.4 1-.2 1.1.4 2.3.6 3.6.6.6 0 1 .4 1 1V20c0 .6-.4 1-1 1A17 17 0 0 1 3 4c0-.6.4-1 1-1h3.5c.6 0 1 .4 1 1 0 1.3.2 2.5.6 3.6.1.3 0 .7-.2 1z"/></svg>
      (555) 274-3918
    </li>
    <li class="contacts__item">
      <svg class="contacts__icon" viewBox="0 0 24 24" aria-hidden="true"><path d="M2 5h20v2l-10 6L2 7z"/><path d="M2 9.3l10 6 10-6V19H2z"/></svg>
      g.harlow@bayfieldcapitalworks.example
    </li>
    <li class="contacts__item">
      <svg class="contacts__icon" viewBox="0 0 24 24" aria-hidden="true"><circle cx="12" cy="12" r="10"/><path d="M8 6c2 1 3 3 1 5s1 4 3 4 1 3 0 4M15 4c-1 2 1 3 3 3" stroke="#fff" stroke-width="1.6" fill="none"/></svg>
      www.bayfieldcapitalworks.example
    </li>
  </ul>
</section>

<section class="card card--back">
  <div class="back-brand">
    <span class="back-brand__mark"></span>
    <p class="back-brand__name">BAYFIELD CAPITAL WORKS, INC</p>
    <p class="back-brand__tagline">Trusted guidance for every local ownership move</p>
  </div>
</section>

</body>
</html>
```